Business cards for a fun web development agency

Hi,I am building a web development agency. You can read about it on the website http://kite-loft.examplehost.com. Basically, I want to focus on free and open source products and stay as far away from the corporate business feeling as possible. I want to build a community so I want the business card to feel fun and approachable (at the risk of professional if need be). I am uploading some of my image assets in various file formats. Feel free to use them or make your own if you want just keeping in theme with the website.
Industry/Entity Type
Building
Contact Information for Business Card
Company Name: Boat ShedWebsite: www.kiteloftdev.example (it's currently in alpha on http://kite-loft.examplehost.com if you want to see the them we are trying to capture)My name is: Banner B. SchaferMy email: banner@boatsheddev.comMy phone: 0431 587 904
Look and feel

```html
<!DOCTYPE html>
<html lang="en">
<head>
<meta charset="utf-8">
<title>Kite Loft – Business Cards</title>
<link rel="stylesheet" href="https://fonts.googleapis.com/css2?family=Arimo:wght@400;700&display=swap">
<style>
  :root {
    --page-bg: #e9ecef;
    --card-white: #ffffff;
    --card-shade: #eef1f4;
    --brand-cyan: #1fa9c9;
    --brand-deep: #2a77a8;
    --stripe-light: #5cc6de;
    --sky-top: #cdeef5;
    --sky-low: #9fd9e8;
    --sea-top: #6fbfd7;
    --sea-low: #8ccfe0;
    --contact-ink: #3d78a6;
    --shadow: rgba(20, 40, 60, 0.18);
  }
  * { box-sizing: border-box; margin: 0; padding: 0; }
  html, body {
    width: 1200px;
    height: 885px;
    overflow: hidden;
    background: var(--page-bg);
    font-family: "Arimo", Arial, sans-serif;
  }
  .sheet {
    width: 1200px;
    height: 885px;
    display: flex;
    flex-direction: column;
    align-items: center;
    justify-content: center;
    gap: 40px;
  }
  .card {
    width: 680px;
    height: 388px;
    background: var(--card-white);
    box-shadow: 0 6px 18px var(--shadow);
    position: relative;
    overflow: hidden;
  }

  /* Front */
  .card-front { display: flex; flex-direction: column; }
  .front-brand {
    height: 118px;
    display: flex;
    align-items: center;
    justify-content: center;
    gap: 18px;
  }
  .brand-dot {
    width: 52px;
    height: 52px;
    border-radius: 50%;
    background: var(--brand-cyan);
  }
  .brand-name {
    font-size: 66px;
    font-weight: 400;
    letter-spacing: 1px;
    color: var(--brand-cyan);
    text-transform: uppercase;
    line-height: 1;
  }
  .front-band {
    flex: 1;
    display: flex;
    flex-direction: column;
  }
  .band-stripe { height: 7px; background: var(--brand-cyan); }
  .band-stripe.thin { height: 3px; background: var(--stripe-light); margin-top: 3px; }
  .band-stripe.thin.before { margin-top: 0; margin-bottom: 3px; }
  .band-scene {
    flex: 1;
    background: linear-gradient(180deg, var(--sky-top) 0%, var(--sky-low) 42%, var(--sea-top) 44%, var(--sea-low) 100%);
  }
  .front-tagline {
    height: 56px;
    display: flex;
    align-items: center;
    justify-content: center;
    font-size: 17px;
    color: var(--brand-cyan);
    gap: 10px;
  }
  .tag-divider { color: var(--brand-deep); }

  /* Back */
  .card-back {
    background: radial-gradient(ellipse at 45% 40%, var(--card-white) 0%, var(--card-shade) 100%);
  }
  .contact {
    position: absolute;
    left: 250px;
    top: 96px;
  }
  .contact-name {
    font-size: 38px;
    color: var(--brand-cyan);
    margin-bottom: 20px;
  }
  .contact-line {
    font-size: 25px;
    color: var(--contact-ink);
    line-height: 1.45;
  }
</style>
</head>
<body>
<main class="sheet">
  <section class="card card-front">
    <div class="front-brand">
      <span class="brand-dot"></span>
      <span class="brand-name">Kite Loft</span>
    </div>
    <div class="front-band">
      <div class="band-stripe"></div>
      <div class="band-stripe thin before"></div>
      <div class="band-scene" role="img" aria-label="Illustration of a small blue shed on a jetty over calm sea under a pale sky"></div>
      <div class="band-stripe thin"></div>
      <div class="band-stripe"></div>
    </div>
    <div class="front-tagline">
      <span>Open Source Software</span><span class="tag-divider">|</span>
      <span>Consulting For Developers</span><span class="tag-divider">|</span>
      <span>Web Development For Muggles</span>
    </div>
  </section>

  <section class="card card-back">
    <div class="contact">
      <p class="contact-name">Corwin T. Aldous</p>
      <p class="contact-line">0431 587 904</p>
      <p class="contact-line">www.kiteloftdev.example</p>
      <p class="contact-line">corwin@kiteloftdev.example</p>
    </div>
  </section>
</main>
</body>
</html>
```